Theatre Company needs a Poster design for a world premiere of "The Lantern" Play.

We are premiering a play that celebrates community in rural and regional Australia . We need a poster for A3 and A5 size and an image that can be used in our email correspondence/webpage.

Attached is some ideas the producing theatre committee has come up with, a river runs through the town itself.

Town

```html
<!DOCTYPE html>
<html lang="en">
<head>
<meta charset="utf-8">
<title>The Lantern — Poster</title>
<link rel="stylesheet" href="https://fonts.googleapis.com/css2?family=Bodoni+Moda:wght@400&family=Playfair+Display:ital,wght@0,400;1,400&display=swap">
<style>
  :root {
    --night: #0a0a0b;
    --stone: #6f7377;
    --stone-light: #c9ccce;
    --water: #2a2d30;
    --maroon: #4b1a1d;
    --maroon-veil: rgba(128, 32, 38, 0.62);
    --rule: #1c0a0b;
    --cream: #f3ebe6;
  }
  html, body {
    margin: 0;
    padding: 0;
    width: 849px;
    height: 1200px;
    overflow: hidden;
    background: var(--night);
  }
  .poster {
    position: relative;
    width: 849px;
    height: 1200px;
    overflow: hidden;
    background: var(--night);
  }
  .scene {
    position: absolute;
    inset: 0;
    background:
      linear-gradient(180deg,
        var(--night) 0%,
        var(--night) 44%,
        #3a3d40 50%,
        var(--stone) 55%,
        var(--stone-light) 59%,
        #8c9094 64%,
        #45494c 72%,
        var(--water) 80%,
        #3b3f42 88%,
        #15171a 100%);
  }
  .graphics {
    position: absolute;
    inset: 0;
  }
  .presenter,
  .title,
  .credit,
  .tagline {
    position: absolute;
    margin: 0;
    color: var(--cream);
  }
  .presenter {
    left: 72px;
    top: 292px;
    width: 546px;
    font-family: "Playfair Display", Georgia, serif;
    font-size: 18.5px;
    letter-spacing: 0.4px;
    text-transform: uppercase;
    white-space: nowrap;
  }
  .title {
    left: 60px;
    top: 352px;
    width: 560px;
    text-align: center;
    font-family: "Bodoni Moda", "Didot", serif;
    font-weight: 400;
    font-size: 80px;
    line-height: 110px;
    letter-spacing: 1px;
    text-transform: uppercase;
    white-space: nowrap;
  }
  .credit {
    right: 232px;
    top: 505px;
    font-family: "Playfair Display", Georgia, serif;
    font-size: 18px;
    letter-spacing: 0.3px;
    text-transform: uppercase;
    white-space: nowrap;
  }
  .tagline {
    left: 233px;
    top: 1099px;
    width: 602px;
    height: 69px;
    line-height: 69px;
    text-align: center;
    font-family: "Playfair Display", Georgia, serif;
    font-style: italic;
    font-size: 30px;
    white-space: nowrap;
  }
</style>
</head>
<body>
  <main class="poster">
    <div class="scene" role="img" aria-label="Night photograph of a stone arched bridge lit by lamps, reflected in a dark river"></div>

    <svg class="graphics" width="849" height="1200" viewBox="0 0 849 1200" aria-hidden="true">
      <defs>
        <clipPath id="disc-clip">
          <circle cx="321" cy="409" r="321"/>
        </clipPath>
      </defs>
      <circle class="disc" cx="321" cy="409" r="321" fill="var(--maroon-veil)"/>
      <g clip-path="url(#disc-clip)">
        <rect class="disc-shade" x="0" y="80" width="660" height="500" fill="var(--maroon)" opacity="0.55"/>
        <rect class="rule" x="0" y="339" width="660" height="3" fill="var(--rule)"/>
        <rect class="rule" x="0" y="474" width="660" height="3" fill="var(--rule)"/>
      </g>
      <rect class="tagline-band" x="233" y="1099" width="602" height="69" fill="var(--maroon-veil)"/>
      <rect class="tagline-rule" x="233" y="1104" width="602" height="1.5" fill="var(--rule)"/>
      <rect class="tagline-rule" x="233" y="1162" width="602" height="1.5" fill="var(--rule)"/>
    </svg>

    <p class="presenter">Wattlebank Theatre Company presents to you</p>
    <h1 class="title">The Lantern</h1>
    <p class="credit">Written by Nell Brannigan</p>
    <p class="tagline">“a river runs through the town itself”</p>
  </main>
</body>
</html>
```